Mobile Friendly Lead Generation Landing Page

We are a web marketing company that specialized in web lead generation. Recently we have started buying media from mobile devices and we need a mobile interface(landing page) where we can collect user data in an effective manner.

Our current mobile landing page is:
http://www.tutorpath.example.com/lp13d/index.aspx?a=true&source=841356
Through this you can see what the steps/questions users need to answer to get matched to a school. We need the design for the whole process.

We are pretty open for design ideas and our goal is to make this mobile optimized landing page have the look and feel of an app...but not an app.
There are several questions in the process but we are open to changing the way they are presented. As in, you can have one question at a time or a few.
The goal is to make this EXTREMELY EASY for users to interact with.

One example that we have liked is:
http://learnvane.example/schools/57214-page1.lvne (please note that this opens only on mobile devices)

Some of these screenshots are attached.

Our web form looks like this:
http://www.tutorpath.example.com/lp88/index.aspx?a=true

```html
<!DOCTYPE html>
<html lang="en">
<head>
<meta charset="utf-8">
<title>TutorPath – Get Matched</title>
<link rel="stylesheet" href="https://fonts.googleapis.com/css2?family=Roboto:wght@300;400;500&display=swap">
<style>
  :root {
    --page-bg: #ffffff;
    --brand-band: #f8f5ea;
    --hero-light: #f6efe2;
    --hero-warm: #e6c89f;
    --hero-cool: #c9d3dc;
    --ink-dark: #151515;
    --ink-grey: #5f5f5f;
    --accent-blue: #1b8fe3;
    --accent-blue-deep: #0a6fc4;
    --track: #dfe3ea;
    --field-bg: #f5f5f5;
    --field-line: #e6e6e6;
    --placeholder: #a9a9a9;
    --label: #555555;
    --button-bg: #efefef;
    --button-line: #bdbdbd;
    --button-icon: #4a4a4a;
  }
  * { box-sizing: border-box; margin: 0; padding: 0; }
  html, body {
    width: 1200px;
    height: 2773px;
    overflow: hidden;
    background: var(--page-bg);
    font-family: "Roboto", "Helvetica Neue", Arial, sans-serif;
  }
  .landing {
    position: relative;
    width: 1200px;
    height: 2773px;
  }
  .brand-bar {
    position: absolute;
    left: 0; top: 0;
    width: 1200px; height: 146px;
    background: var(--brand-band);
    display: flex;
    align-items: center;
    justify-content: center;
  }
  .brand-name {
    font-weight: 500;
    font-size: 50px;
    color: var(--ink-dark);
    letter-spacing: -0.5px;
  }
  .hero {
    position: absolute;
    left: 0; top: 146px;
    width: 1200px; height: 450px;
    overflow: hidden;
  }
  .hero-photo {
    position: absolute;
    inset: 0;
    background:
      radial-gradient(ellipse 380px 300px at 820px 170px, var(--hero-cool) 0%, rgba(201,211,220,0) 70%),
      radial-gradient(ellipse 520px 360px at 960px 330px, var(--hero-warm) 0%, rgba(230,200,159,0) 75%),
      linear-gradient(90deg, var(--hero-light) 0%, #f1e4cf 55%, #e9d2b0 100%);
  }
  .hero-headline {
    position: absolute;
    left: 44px;
    top: 72px;
    letter-spacing: -3px;
  }
  .hero-line { display: block; white-space: nowrap; }
  .hero-line--lead {
    font-weight: 400;
    font-size: 84px;
    line-height: 94px;
    color: var(--ink-dark);
  }
  .hero-line--main {
    font-weight: 300;
    font-size: 100px;
    line-height: 108px;
    color: var(--ink-grey);
  }
  .hero-line--cta {
    font-weight: 300;
    font-size: 100px;
    line-height: 108px;
    color: var(--accent-blue);
  }
  .progress {
    position: absolute;
    left: 24px; top: 657px;
    width: 1156px; height: 26px;
    border-radius: 6px;
    background: var(--track);
    overflow: hidden;
  }
  .progress-fill {
    width: 67%;
    height: 100%;
    border-radius: 6px;
    background: linear-gradient(180deg, var(--accent-blue) 0%, var(--accent-blue-deep) 100%);
  }
  .lead-form {
    position: absolute;
    left: 24px; top: 750px;
    width: 1156px;
  }
  .form-title {
    font-weight: 400;
    font-size: 53px;
    color: var(--label);
    letter-spacing: -0.5px;
    margin-bottom: 62px;
  }
  .field {
    height: 141px;
    margin-bottom: 18px;
    background: var(--field-bg);
    border: 2px solid var(--field-line);
    border-radius: 6px;
    display: flex;
    align-items: center;
    padding-left: 35px;
    font-weight: 300;
    font-size: 44px;
    color: var(--placeholder);
  }
  .submit {
    position: absolute;
    left: 514px;
    top: 777px;
    width: 128px; height: 128px;
    border-radius: 50%;
    background: var(--button-bg);
    border: 3px solid var(--button-line);
    display: flex;
    align-items: center;
    justify-content: center;
  }
</style>
</head>
<body>
<main class="landing">
  <header class="brand-bar">
    <span class="brand-name">TutorPath</span>
  </header>

  <section class="hero">
    <div class="hero-photo" role="img" aria-label="Soft-focus photo of a student relaxing outdoors in warm light"></div>
    <h1 class="hero-headline">
      <span class="hero-line hero-line--lead">GET MATCHED TO</span>
      <span class="hero-line hero-line--main">Online &amp; Local Colleges</span>
      <span class="hero-line hero-line--cta">Now!</span>
    </h1>
  </section>

  <div class="progress" aria-label="Step progress">
    <div class="progress-fill"></div>
  </div>

  <form class="lead-form">
    <h2 class="form-title">Your Personal Information:</h2>
    <div class="field">First Name</div>
    <div class="field">Last Name</div>
    <div class="field">Email Address</div>
    <div class="field">Phone Number</div>
    <div class="submit" aria-label="Continue">
      <svg width="34" height="38" viewBox="0 0 34 38" aria-hidden="true">
        <polygon points="6,4 30,19 6,34" fill="var(--button-icon)"/>
      </svg>
    </div>
  </form>
</main>
</body>
</html>
```